eCommerce website for a DIY shop & communal center

We need a website for a business called The Maple Bench. The Maple Bench is both a shop and communal establishment where people with shared interests, especially in DIY (Do It Yourself) and crafting, can gather to shop for & work on projects while sharing ideas, equipment, supplies and knowledge. The shop is both brick & motor and online. The physical communal space provides workstations, equipment, tools and supplies and expertise for DIY lovers to create their projects.

Target Market(s)

Middle & upper class DIY enthusiasts, creative hobbyists, budding artists & small business owners

Industry/Entity Type

DIY, Arts & Crafts

Coding

Coded - Design and coding required

Number of Pages Required

5+ page

Requirements
Must have
• Menus to include 1. home page (with about us, operating hours, contacts, location, meet the team); 2. Bench activities (how to DIY at the Bench, booking, equipment & tools, house rules); 3. Bench events (events in the Bench, offsite events); 4. Resources (FAQs, tutorials, blogs, eBooks) and 5. Online shop
Nice to have
• Branding guidelines eg logo colours (see attachment) to influence design. Tillpost shop. Booking feature for activities & events at the Bench.

```html
<!DOCTYPE html>
<html lang="en">
<head>
<meta charset="utf-8">
<title>The Maple Bench</title>
<link rel="stylesheet" href="https://fonts.googleapis.com/css2?family=Roboto:ital,wght@0,400;0,500;0,700;1,400;1,500&family=Great+Vibes&display=swap">
<style>
:root{
  --orange:#f0773a;
  --orange-light:#f5894c;
  --blue:#2a8ad6;
  --ink:#222;
  --muted:#555;
  --white:#fff;
  --footer:#0d0d0d;
  --wash-blue:#bfe0f2;
  --wash-peach:#f9cdb4;
}
*{box-sizing:border-box;margin:0;padding:0}
html,body{width:1200px;height:4898px;overflow:hidden;background:var(--white)}
body{position:relative;font-family:'Roboto',sans-serif;color:var(--ink)}
.abs{position:absolute}
.script{font-family:'Great Vibes',cursive;font-weight:400;font-size:48px;line-height:1}
.script .o{color:var(--orange)}
.script .b{color:var(--blue)}
.btn{position:absolute;display:flex;align-items:center;justify-content:center;background:var(--orange);color:var(--white);font-size:13px;font-weight:500;border-radius:24px;text-transform:uppercase;letter-spacing:.3px}
.lead{position:absolute;text-align:center;font-size:13.5px;line-height:25px;color:var(--muted)}
.photo{position:absolute}

/* header */
.header{position:absolute;left:0;top:0;width:1200px;height:100px;background:var(--white)}
.phone{position:absolute;left:100px;top:8px;display:flex;align-items:center;gap:12px;font-size:14px;color:var(--ink)}
.phone .ic{width:32px;height:32px;border:1.5px solid #999;border-radius:50%;display:flex;align-items:center;justify-content:center}
.socials-top{position:absolute;left:928px;top:6px;display:flex;gap:8px}
.socials-top span{width:34px;height:34px;border:1.5px solid #999;border-radius:50%}
.nav a{position:absolute;top:64px;font-size:14.5px;color:var(--ink);text-decoration:none;font-weight:500}
.brand{position:absolute;left:520px;top:0;width:160px;height:132px;background:var(--white);border-radius:0 0 80px 80px;display:flex;flex-direction:column;align-items:center;justify-content:center;gap:6px;z-index:2}
.brand .dot{width:14px;height:14px;border-radius:50%;background:var(--orange)}
.brand .name{font-size:17px;font-weight:700;color:var(--orange);text-align:center;line-height:20px}

/* hero */
.hero{left:0;top:100px;width:1200px;height:565px;background:linear-gradient(100deg,#4a3424 0%,#6a4a30 35%,#8a6446 60%,#5c3f2b 100%)}
.hero h1{position:absolute;left:103px;top:198px;font-size:50px;line-height:54px;font-weight:700;color:var(--white);text-transform:uppercase;letter-spacing:-.5px}
.dots{position:absolute;left:556px;top:524px;display:flex;gap:12px}
.dots span{width:11px;height:11px;border:1.5px solid #fff;border-radius:50%}
.dots span.on{background:#fff}

/* steps */
.step{position:absolute;top:917px;width:230px}
.step .frame{position:absolute;left:18px;top:0;width:192px;height:190px;border:4px solid var(--blue)}
.step .circle{position:absolute;left:12px;top:10px;width:204px;height:172px;border-radius:50%}
.step h3{position:absolute;top:212px;width:230px;text-align:center;font-size:15px;font-style:italic;font-weight:500;color:var(--ink)}
.step h3 b{color:var(--orange);font-weight:400}
.step p{position:absolute;top:240px;width:230px;text-align:center;font-size:11.5px;line-height:21px;color:var(--muted)}

/* about */
.about{left:0;top:1422px;width:1200px;height:482px;background:linear-gradient(90deg,#9a5a38,#a8613a 50%,#8e4f30)}
.about-art{left:40px;top:1422px;width:590px;height:482px}
.about .title{position:absolute;left:660px;top:92px;color:var(--white)}
.about p{position:absolute;left:660px;top:162px;width:450px;font-size:13.5px;line-height:27px;color:#f5e8df}

/* washes */
.wash{position:absolute;border-radius:50%;filter:blur(18px)}

/* featured */
.feat{position:absolute;top:2130px;width:320px;height:370px}
.cap{position:absolute;top:2518px;width:320px;text-align:center;font-size:20px;color:var(--ink)}

/* hours */
.hours{position:absolute;left:200px;top:2870px;font-size:14px;line-height:29.5px}
.hours .day{position:absolute;left:0;width:180px;text-align:right}
.hours .time{position:absolute;left:262px;width:100px}

/* location */
.loc p{position:absolute;font-size:15px;color:var(--ink)}

/* footer */
.footer{left:0;top:4552px;width:1200px;height:346px;background:var(--footer);color:var(--white)}
.fcol{position:absolute;top:82px}
.fcol h4{font-size:14.5px;font-weight:700;margin-bottom:14px;letter-spacing:.3px}
.fcol li{list-style:none;font-size:13px;line-height:28px}
.email{position:absolute;left:842px;top:110px;width:258px;height:43px;background:var(--white);border-radius:22px;color:#444;font-size:12.5px;padding:14px 16px}
.sub{left:842px;top:163px;width:258px;height:42px}
.socials-foot{position:absolute;left:852px;top:220px;display:flex;gap:10px}
.socials-foot span{width:34px;height:34px;border-radius:50%;background:var(--white)}
.copy{position:absolute;top:310px;width:1200px;text-align:center;font-size:12px;color:#ddd}
</style>
</head>
<body>

<header class="header">
  <div class="phone">
    <span class="ic"><svg width="16" height="16" viewBox="0 0 24 24"><path d="M6.6 10.8a15 15 0 0 0 6.6 6.6l2.2-2.2a1 1 0 0 1 1-.25 11.4 11.4 0 0 0 3.6.6 1 1 0 0 1 1 1V20a1 1 0 0 1-1 1A17 17 0 0 1 3 4a1 1 0 0 1 1-1h3.5a1 1 0 0 1 1 1c0 1.25.2 2.45.6 3.6a1 1 0 0 1-.25 1z" fill="#666"/></svg></span>
    555 - 014 - 2290
  </div>
  <nav class="nav">
    <a style="left:100px">HOME</a>
    <a style="left:194px">BENCH ACTIVITIES</a>
    <a style="left:380px">BENCH EVENTS</a>
    <a style="left:703px">RESOURCES</a>
    <a style="left:848px">ONLINE SHOP</a>
    <a style="left:1007px">CONTACT US</a>
  </nav>
  <div class="socials-top" aria-label="Social links"><span></span><span></span><span></span><span></span></div>
</header>
<div class="brand"><span class="dot"></span><span class="name">The Maple<br>Bench</span></div>

<section class="abs hero" role="img" aria-label="Woman working on a wooden craft project at a workshop bench">
  <h1>Tap into your<br>crafty side!</h1>
  <div class="btn" style="left:100px;top:330px;width:182px;height:47px">Get Started</div>
  <div class="dots"><span></span><span class="on"></span><span></span><span></span></div>
</section>

<h2 class="abs script" style="left:0;top:750px;width:1200px;text-align:center"><span class="o">Any</span> <span class="b">Craft,</span> <span class="o">Any</span> <span class="b">Time</span></h2>
<p class="lead" style="left:250px;top:822px;width:700px">Lorem ipsum dolor sit amet, consectetur adipiscing elit, sed do eiusmod tempor incididunt ut labore et dolore magna aliqua. Quis ipsum suspendisse ultrices gravida.</p>

<div class="step" style="left:99px">
  <div class="frame"></div><div class="circle" role="img" aria-label="Customer choosing a DIY kit from a shelf" style="background:linear-gradient(135deg,#7c8a96,#3f4650)"></div>
  <h3><b>1.</b> Choose Your DIY</h3>
  <p>Lorem ipsum dol, consectetdipiscing elit, sed do eiusmod temporcididunt ut labore et dolore maalQuis ipsum suspendisse ultrices gravida.</p>
</div>
<div class="step" style="left:356px">
  <div class="frame"></div><div class="circle" role="img" aria-label="Laptop on a desk for making a reservation" style="background:linear-gradient(135deg,#e6ddd2,#b8aa98)"></div>
  <h3><b>2.</b> Make a reservation or walk in</h3>
  <p>Lorem ipsum dol, consectetdipiscing elit, sed do eiusmod temporcididunt ut labore et dolore maalQuis ipsum suspendisse ultrices gravida.</p>
</div>
<div class="step" style="left:613px">
  <div class="frame"></div><div class="circle" role="img" aria-label="Group crafting together at a table" style="background:linear-gradient(135deg,#c9a48a,#8a5e48)"></div>
  <h3><b>3.</b> Have fun!</h3>
  <p>Lorem ipsum dol, consectetdipiscing elit, sed do eiusmod temporcididunt ut labore et dolore maalQuis ipsum suspendisse ultrices gravida.</p>
</div>
<div class="step" style="left:870px">
  <div class="frame"></div><div class="circle" role="img" aria-label="Finished embroidered craft piece" style="background:linear-gradient(135deg,#b08a6a,#7a2a2a)"></div>
  <h3><b>4.</b> Take it home</h3>
  <p>Lorem ipsum dol, consectetdipiscing elit, sed do eiusmod temporcididunt ut labore et dolore maalQuis ipsum suspendisse ultrices gravida.</p>
</div>
<div class="btn" style="left:509px;top:1282px;width:181px;height:46px">Book a Project</div>

<section class="abs about" role="img" aria-label="Brick wall background">
  <h2 class="script title">About Us</h2>
  <p>Sed ut perspiciatis unde omnis iste natus errluptatem accusantium doloremque laudantium, totam rem aperiam, eaque ipsa quae ab illo inventore veritatis et quasi architecto beatae e dicta sunt explicabo. Nemo enim ipsam voluptatem quia voluptas sit aspernatur aut odit aut fugit, sed quia consequuntur magni eos qui ratione voluptatem sequi nesciunt. Neque porro quisquam</p>
  <div class="btn" style="left:660px;top:346px;width:180px;height:47px">Learn More</div>
</section>
<div class="abs about-art" role="img" aria-label="Four smiling friends holding oversized paint swatches, hammer, drill and scissors" style="background:linear-gradient(135deg,rgba(230,200,170,.5),rgba(160,100,70,.3))"></div>

<h2 class="abs script" style="left:0;top:1988px;width:1200px;text-align:center"><span class="o">Featured</span> <span class="b">Projects</span></h2>
<p class="lead" style="left:250px;top:2050px;width:700px">Lorem ipsum dolor sit amet, consectetur adipiscing elit, sed do eiusmod tempor incididunt ut labore et dolore magna aliqua. Quis ipsum suspendisse ultrices gravida.</p>

<div class="wash" role="img" aria-label="Soft blue watercolor wash" style="left:-20px;top:2330px;width:1240px;height:300px;background:radial-gradient(ellipse at 50% 50%,var(--wash-blue),rgba(191,224,242,.4) 60%,transparent 75%)"></div>
<div class="wash" style="left:250px;top:2460px;width:600px;height:180px;background:radial-gradient(ellipse,rgba(249,205,180,.7),transparent 70%)"></div>

<div class="feat" role="img" aria-label="Pineapple string art on a wooden board" style="left:100px;background:linear-gradient(135deg,#eceae6,#8a5a38 40%,#c9b08a)"></div>
<div class="feat" role="img" aria-label="Twine wrapped bottles with roses" style="left:440px;background:linear-gradient(135deg,#f2ede6,#d8b8a0 50%,#e88a7a)"></div>
<div class="feat" role="img" aria-label="Unicorn decorated eggs in a wreath" style="left:778px;background:linear-gradient(135deg,#f08a9a,#eef0f0 50%,#62b8d8)"></div>
<p class="cap" style="left:100px">Sed ut perspiciatis und</p>
<p class="cap" style="left:440px">Sed ut perspiciatis und</p>
<p class="cap" style="left:778px">Sed ut perspiciatis und</p>

<div class="wash" role="img" aria-label="Peach watercolor wash" style="left:60px;top:2740px;width:520px;height:360px;background:radial-gradient(ellipse,var(--wash-peach),rgba(249,205,180,.5) 55%,transparent 72%)"></div>
<h2 class="abs script" style="left:275px;top:2790px"><span class="o">Operating</span> <span class="b">Hours</span></h2>
<div class="hours">
  <span class="day" style="top:0">Monday</span><span class="time" style="top:0">09.30 – 20.00</span>
  <span class="day" style="top:29.5px">Tuesday</span><span class="time" style="top:29.5px">09.30 – 20.00</span>
  <span class="day" style="top:59px">Wednesday</span><span class="time" style="top:59px">09.30 – 20.00</span>
  <span class="day" style="top:88.5px">Thursday</span><span class="time" style="top:88.5px">09.30 – 20.00</span>
  <span class="day" style="top:118px">Friday</span><span class="time" style="top:118px">09.30 – 18.00</span>
  <span class="day" style="top:147.5px">Saturday</span><span class="time" style="top:147.5px">09.30 – 17.00</span>
  <span class="day" style="top:177px">Sunday</span><span class="time" style="top:177px">11.00 – 17.00</span>
</div>
<div class="photo" role="img" aria-label="People crafting at long tables in the workshop" style="left:600px;top:2760px;width:500px;height:412px;background:linear-gradient(135deg,#d8dde0,#8f959a 50%,#5c5450)"></div>

<div class="photo" role="img" aria-label="Shop building exterior under blue sky" style="left:100px;top:3258px;width:500px;height:412px;background:linear-gradient(180deg,#2f6bb8 0%,#4f8bd0 35%,#e6c8a2 55%,#d8b88e 80%,#7a8a6a 100%)"></div>
<div class="wash" role="img" aria-label="Blue watercolor wash" style="left:600px;top:3280px;width:560px;height:330px;background:radial-gradient(ellipse,rgba(191,224,242,.85),rgba(191,224,242,.3) 60%,transparent 74%)"></div>
<h2 class="abs script" style="left:640px;top:3290px"><span class="o">Our</span> <span class="b">Location</span></h2>
<div class="loc">
  <p style="left:642px;top:3366px">48 Alder Lane Springvale USA</p>
  <p style="left:642px;top:3394px">20417</p>
  <p style="left:642px;top:3434px;width:420px;font-size:14.5px;line-height:29px">Sed ut perspiciatis unde omnis iste natus error sit voluptatem accusantium doloremque laudantium, totam rem aperiam, eaque ipsa quae ab</p>
</div>
<div class="btn" style="left:638px;top:3534px;width:180px;height:46px">Contact Us</div>

<h2 class="abs script" style="left:0;top:3770px;width:1200px;text-align:center"><span class="o">Private</span> <span class="o">Events</span></h2>
<p class="lead" style="left:148px;top:3832px;width:904px">Sed ut perspiciatis unde omnis iste natus error sit voluptatem accusantium doloremque laudantium, totam rem aperiam, eaque ipsa quae ab illo inventore veritatis et quasi architecto beatae vitae dicta sunt explicabo. Nemo enim ipsam voluptatem quia voluptas sit aspernatur aut odit aut fugit, sed quia consequuntur magni dolores eos qui ratione voluptatem sequi nesciunt. Neque porro quisquam est, qui dolorem ipsum quia dolor sit amet, consectetur</p>
<div class="wash" role="img" aria-label="Blue watercolor wash" style="left:-20px;top:4200px;width:1240px;height:260px;background:radial-gradient(ellipse,var(--wash-blue),rgba(191,224,242,.35) 60%,transparent 75%)"></div>
<div class="photo" role="img" aria-label="Hands painting Easter eggs" style="left:100px;top:3970px;width:320px;height:325px;background:linear-gradient(135deg,#f4eef0,#e8a0c0 45%,#7ab0c8)"></div>
<div class="photo" role="img" aria-label="Hands shaping clay on a pottery wheel" style="left:440px;top:3970px;width:320px;height:325px;background:linear-gradient(135deg,#3a3a3c,#8a8278 50%,#c8c0b4)"></div>
<div class="photo" role="img" aria-label="Parent and child building a woodworking project" style="left:778px;top:3970px;width:320px;height:325px;background:linear-gradient(135deg,#5a4a3a,#8a4a8a 40%,#d8c8b0)"></div>
<div class="btn" style="left:444px;top:4332px;width:312px;height:46px">Contact Us to Book Your Event</div>

<footer class="abs footer">
  <div class="fcol" style="left:100px"><h4>ABOUT</h4><ul><li>Our Story</li><li>Press</li><li>Locations</li><li>Blog</li><li>Contact Us</li></ul></div>
  <div class="fcol" style="left:236px"><h4>OUR OFFERING</h4><ul><li>Projects</li><li>Color Room</li><li>Parties</li><li>Classes</li></ul></div>
  <div class="fcol" style="left:421px"><h4>OTHER</h4><ul><li>Franchise</li><li>Gift Cards</li><li>FAQ</li><li>Refund Policy</li></ul></div>
  <div class="fcol" style="left:571px"><h4>CONTACT US</h4><ul><li>48 Alder Lane Springvale USA</li><li>20417</li><li>555 - 014 - 2290</li><li>info@maplebench.com</li></ul></div>
  <div class="fcol" style="left:842px"><h4>GET UPDATES &amp; PROMOS</h4></div>
  <div class="email">Email Address</div>
  <div class="btn sub">Subscribe</div>
  <div class="socials-foot" aria-label="Social links"><span></span><span></span><span></span><span></span></div>
  <p class="copy">Copyright © 2021 The Maple Bench. All rights reserved.</p>
</footer>

</body>
</html>
```